Brisbane IT support business needs our first website

Hi All,

We are after a new website design for our IT solutions and support business.The business name is Harbourline Computing Services Group, or HCSG for short. We provide a range of solutions and services within the IT space.

I would like to utilize the two colours in our business logo I have uploaded.

I understand this is initially for the design only aspect of the site, but I would like to engage the winner to finish coding the website and finalize after also.

Target Market(s)

Other businesses owners and home users.

Industry/Entity Type

Business

Requirements
Must have
• Nice clean and functional design utilizing our business colours from the logo.

```html
<!DOCTYPE html>
<html lang="en">
<head>
<meta charset="utf-8">
<title>HCSG – IT Solutions and Support</title>
<link href="https://fonts.googleapis.com/css2?family=Open+Sans:ital,wght@0,400;0,600;0,700;1,700&display=swap" rel="stylesheet">
<style>
:root{
  --teal:#0d4c66;
  --teal-mid:#1a6e8e;
  --teal-dark:#0a3b50;
  --orange:#f08a1c;
  --orange-dark:#d97610;
  --ink:#333b40;
  --muted:#6b7479;
  --line:#d9dee1;
  --card:#eef1f3;
  --white:#ffffff;
}
*{box-sizing:border-box;margin:0;padding:0}
html,body{width:1200px;height:2272px;overflow:hidden}
body{position:relative;background:var(--white);font-family:"Open Sans",Arial,sans-serif;color:var(--ink)}
.abs{position:absolute}

/* header */
.brand{left:60px;top:22px;display:flex;align-items:center;gap:16px}
.brand-mark{width:92px;height:92px;border-radius:50%;background:var(--teal)}
.brand-name{font-size:58px;font-weight:700;color:var(--orange);line-height:1}
.brand-tag{font-size:11px;font-weight:600;color:var(--teal);margin-top:4px;width:210px;line-height:1.3}
.social{display:flex;gap:8px}
.social span{width:26px;height:26px;border-radius:50%;background:var(--teal-mid)}
.top-social{right:60px;top:18px}
.top-phone{right:60px;top:54px;display:flex;align-items:center;gap:10px;font-size:28px;font-weight:700;color:var(--ink)}
.top-mail{right:60px;top:96px;font-size:13px;color:var(--muted)}

/* nav */
.nav{left:0;top:138px;width:1200px;height:44px;background:var(--teal);display:flex;justify-content:center}
.nav a{color:var(--white);text-decoration:none;font-size:14px;font-weight:600;padding:0 34px;line-height:44px}
.nav a.active{background:var(--orange)}

/* hero */
.hero{left:0;top:182px;width:1200px;height:520px;background:linear-gradient(120deg,#2c4f63 0%,#6f8ea0 45%,#c9d5dc 75%,#8aa2b0 100%)}
.hero-title{left:110px;top:330px;font-size:46px;font-weight:700;font-style:italic;color:var(--white);line-height:1.25;text-shadow:0 2px 6px rgba(0,0,0,.35)}
.arrow{top:418px;width:50px;height:50px;border-radius:50%;background:rgba(255,255,255,.35);display:flex;align-items:center;justify-content:center}
.dots{left:0;top:716px;width:1200px;display:flex;justify-content:center;gap:8px}
.dots span{width:10px;height:10px;border-radius:50%;background:var(--line)}
.dots span.on{background:var(--teal)}

/* headings */
.sec-head{display:flex;align-items:center;gap:12px;font-size:32px;font-weight:600;color:var(--orange)}
.sec-head i{width:44px;height:44px;border-radius:50%;background:var(--teal);display:block}
.sec-head b{font-weight:600;color:var(--teal)}

/* services */
.services{left:60px;top:820px;width:1080px;display:flex;gap:40px}
.svc{width:240px;height:230px;background:var(--card);border-radius:4px;position:relative;text-align:center;padding-top:62px}
.svc-icon{position:absolute;left:80px;top:-40px;width:80px;height:80px;border-radius:50%;background:var(--teal-mid);border:5px solid var(--white);display:flex;align-items:center;justify-content:center}
.svc h3{font-size:20px;font-weight:600;color:var(--orange)}
.svc p{font-size:12.5px;color:var(--muted);line-height:1.5;margin:10px 22px 12px}
.btn{display:inline-block;background:var(--teal);color:var(--white);font-size:11px;font-weight:700;padding:6px 16px;border-radius:3px}

/* welcome */
.welcome-text{left:60px;top:1180px;width:650px;font-size:13px;line-height:1.6;color:var(--muted)}
.welcome-text p+p{margin-top:14px}
.welcome-img{left:760px;top:1150px;width:380px;height:240px;background:radial-gradient(circle at 45% 50%,#5fa7d6 0%,#1f5f8c 45%,#0c2a45 100%)}

/* columns */
.col{top:1420px;width:330px}
.col h4{font-size:22px;font-weight:600;color:var(--teal);padding-bottom:8px;border-bottom:2px solid var(--line);margin-bottom:14px}
.col h4 b{color:var(--orange);font-weight:600}
.why li{list-style:none;font-size:13px;color:var(--muted);padding:6px 0 6px 22px;position:relative;line-height:1.4}
.why li::before{content:"";position:absolute;left:0;top:11px;width:9px;height:9px;border-radius:50%;background:var(--orange)}
.news-item{display:flex;gap:12px;margin-bottom:16px}
.date{width:48px;height:52px;background:var(--orange);color:var(--white);text-align:center;font-weight:700;font-size:20px;line-height:1.2;padding-top:5px;flex:none}
.date small{display:block;font-size:11px}
.news-item h5{font-size:13px;color:var(--orange);font-weight:700}
.news-item p{font-size:12px;color:var(--muted);line-height:1.4}
.quote{background:var(--card);padding:16px;font-size:12.5px;color:var(--muted);line-height:1.55;font-style:italic}
.quote-by{display:flex;align-items:center;justify-content:space-between;margin-top:12px}
.quote-by span{font-size:12px;font-weight:700;color:var(--orange)}
.quote-photo{width:70px;height:70px;background:linear-gradient(160deg,#b8c3c9,#5e6f79)}

/* clients */
.clients{left:0;top:1790px;width:1200px;height:212px;background:var(--teal)}
.clients h2{text-align:center;color:var(--white);font-size:30px;font-weight:600;margin-top:30px}
.client-row{display:flex;justify-content:center;gap:22px;margin-top:28px}
.client{width:192px;height:80px;background:var(--white);display:flex;align-items:center;justify-content:center;gap:8px;font-size:20px;font-weight:700;color:var(--teal-dark)}
.client i{width:14px;height:14px;background:var(--orange);display:block}

/* footer */
.footer{left:0;top:2002px;width:1200px;height:234px;background:var(--orange)}
.fcol{top:2030px;color:var(--white)}
.fcol h4{font-size:19px;font-weight:600;margin-bottom:14px}
.field{width:240px;height:30px;background:var(--white);border-radius:2px;font-size:12px;color:var(--muted);padding:6px 10px;margin-bottom:8px}
.sub{display:inline-block;background:var(--teal);font-size:13px;font-weight:600;padding:6px 16px;border-radius:2px}
.links{display:flex;gap:50px}
.links ul{list-style:none}
.links li{font-size:13px;line-height:1.9}
.links li::before{content:"› "}
.contact-box{left:400px;top:2168px;width:300px;height:48px;background:var(--teal);display:flex;align-items:center;gap:12px;padding:0 14px;color:var(--white)}
.contact-box em{font-style:normal;font-size:14px;font-weight:700}
.contact-box strong{font-size:22px}
.map{width:250px;height:150px;background:linear-gradient(135deg,#e9e4d6,#cfd8c4 60%,#b9cbd6)}
.bottom{left:0;top:2236px;width:1200px;height:36px;background:var(--teal-dark);display:flex;align-items:center;justify-content:space-between;padding:0 60px;color:var(--white);font-size:12px}
.bottom .social span{width:20px;height:20px;background:var(--orange)}
</style>
</head>
<body>

<header>
  <div class="abs brand">
    <div class="brand-mark"></div>
    <div>
      <div class="brand-name">HCSG</div>
      <div class="brand-tag">Harbourline Computing Services Group</div>
    </div>
  </div>
  <div class="abs social top-social"><span></span><span></span><span></span><span></span></div>
  <div class="abs top-phone">
    <svg width="28" height="28" viewBox="0 0 24 24"><circle cx="12" cy="12" r="12" fill="#0d4c66"/><path d="M8.5 6.5l2 2-1.2 1.6c.7 1.6 2 2.9 3.6 3.6l1.6-1.2 2 2-1.4 2c-4 0-8.6-4.6-8.6-8.6z" fill="#fff"/></svg>
    123-456-7890
  </div>
  <div class="abs top-mail">info@hcsg.example</div>
</header>

<nav class="abs nav">
  <a class="active">HOME</a><a>ABOUT US</a><a>SERVICES</a><a>TECHNOLOGY</a><a>SOLUTIONS</a><a>SUPPORT</a><a>CONTACT US</a>
</nav>

<section>
  <div class="abs hero" role="img" aria-label="Photo of a hand touching a glowing digital interface over a city skyline"></div>
  <h1 class="abs hero-title">We Provide A Range<br>Of Solutions And Services<br>Within The IT Space.</h1>
  <div class="abs arrow" style="left:40px"><svg width="16" height="16" viewBox="0 0 16 16"><path d="M11 2L5 8l6 6" stroke="#fff" stroke-width="2.5" fill="none"/></svg></div>
  <div class="abs arrow" style="right:40px"><svg width="16" height="16" viewBox="0 0 16 16"><path d="M5 2l6 6-6 6" stroke="#fff" stroke-width="2.5" fill="none"/></svg></div>
  <div class="abs dots"><span class="on"></span><span></span><span></span></div>
</section>

<section>
  <div class="abs sec-head" style="left:0;width:1200px;justify-content:center;top:745px"><i></i>OUR SERVICES</div>
  <div class="abs services">
    <div class="svc">
      <div class="svc-icon"><svg width="38" height="38" viewBox="0 0 24 24" fill="none" stroke="#fff" stroke-width="1.8"><circle cx="12" cy="12" r="9"/><path d="M3 12h18M12 3c3 3 3 15 0 18M12 3c-3 3-3 15 0 18"/></svg></div>
      <h3>Website Services</h3>
      <p>Lorem ipsum dolor sit amet, consectetur adipiscing elit, sed diam nonummy nibh euismod.</p>
      <span class="btn">READ MORE ›</span>
    </div>
    <div class="svc">
      <div class="svc-icon"><svg width="38" height="38" viewBox="0 0 24 24" fill="none" stroke="#fff" stroke-width="2"><path d="M14.5 5.5a4 4 0 005 5L12 18l-3 3-3-3 3-3 7.5-7.5zM4 4l6 6"/></svg></div>
      <h3>Hardware &amp; Software</h3>
      <p>Lorem ipsum dolor sit amet, consectetur adipiscing elit, sed diam nonummy nibh euismod.</p>
      <span class="btn">READ MORE ›</span>
    </div>
    <div class="svc">
      <div class="svc-icon"><svg width="38" height="38" viewBox="0 0 24 24" fill="none" stroke="#fff" stroke-width="2"><circle cx="12" cy="12" r="3.5"/><path d="M12 2v4M12 18v4M2 12h4M18 12h4M5 5l3 3M16 16l3 3M5 19l3-3M16 8l3-3"/></svg></div>
      <h3>SEO Services</h3>
      <p>Lorem ipsum dolor sit amet, consectetur adipiscing elit, sed diam nonummy nibh euismod.</p>
      <span class="btn">READ MORE ›</span>
    </div>
    <div class="svc">
      <div class="svc-icon"><svg width="38" height="38" viewBox="0 0 24 24" fill="none" stroke="#fff" stroke-width="2"><rect x="3" y="4" width="18" height="12" rx="1"/><path d="M9 20h6M12 16v4"/></svg></div>
      <h3>Software Development</h3>
      <p>Lorem ipsum dolor sit amet, consectetur adipiscing elit, sed diam nonummy nibh euismod.</p>
      <span class="btn">READ MORE ›</span>
    </div>
  </div>
</section>

<section>
  <div class="abs sec-head" style="left:60px;top:1110px"><i></i><b>WELCOME TO</b> HCSG</div>
  <div class="abs welcome-text">
    <p>Lorem ipsum dolor sit amet, consectetuer adipiscing elit, sed diam nonummy nibh euismod tincidunt ut laoreet dolore magna aliquam erat volutpat. Ut wisi enim ad minim veniam, quis nostrud exerci tation ullamcorper suscipit lobortis nisl ut aliquip ex ea commodo consequat. Duis autem vel eum iriure dolor in hendrerit in vulputate velit esse molestie consequat.</p>
    <p>Lorem ipsum dolor sit amet, consectetuer adipiscing elit, sed diam nonummy nibh euismod tincidunt ut laoreet dolore magna aliquam erat volutpat. Ut wisi enim ad minim veniam, quis nostrud exerci tation ullamcorper suscipit lobortis nisl ut aliquip.</p>
  </div>
  <div class="abs welcome-img" role="img" aria-label="Illustration of a glowing globe with connected network devices"></div>
</section>

<section>
  <div class="abs col" style="left:60px">
    <h4>Why <b>Choose Us</b></h4>
    <ul class="why">
      <li>Lorem ipsum dolor sit amet, consectetur adipiscing elit</li>
      <li>Sed diam nonummy nibh euismod tincidunt ut laoreet</li>
      <li>Lorem ipsum dolor sit amet, consectetur adipiscing elit</li>
      <li>Ut wisi enim ad minim veniam quis nostrud</li>
      <li>Duis autem vel eum iriure dolor in hendrerit</li>
      <li>Lorem ipsum dolor sit amet, consectetur</li>
    </ul>
  </div>
  <div class="abs col" style="left:435px">
    <h4>Latest <b>News</b></h4>
    <div class="news-item"><div class="date">31<small>OCT</small></div><div><h5>Lorem ipsum dolor sit amet...</h5><p>Sed diam nonummy nibh euismod tincidunt ut laoreet dolore magna.</p></div></div>
    <div class="news-item"><div class="date">29<small>OCT</small></div><div><h5>Lorem ipsum dolor sit amet...</h5><p>Sed diam nonummy nibh euismod tincidunt ut laoreet dolore magna.</p></div></div>
    <div class="news-item"><div class="date">27<small>OCT</small></div><div><h5>Lorem ipsum dolor sit amet...</h5><p>Sed diam nonummy nibh euismod tincidunt ut laoreet dolore magna.</p></div></div>
  </div>
  <div class="abs col" style="left:810px">
    <h4>Client <b>Testimonials</b></h4>
    <div class="quote">Lorem ipsum dolor sit amet, consectetuer adipiscing elit, sed diam nonummy nibh euismod tincidunt ut laoreet dolore magna aliquam erat volutpat. Ut wisi enim ad minim veniam.</div>
    <div class="quote-by"><span>— CLIENT NAME, DIRECTOR</span><div class="quote-photo" role="img" aria-label="Portrait photo of the client"></div></div>
  </div>
</section>

<section class="abs clients">
  <h2>Our Clients</h2>
  <div class="client-row">
    <div class="client"><i></i>Quillmark Labs</div>
    <div class="client">Northbeam</div>
    <div class="client"><i></i>Fernway</div>
    <div class="client">Corvella</div>
    <div class="client"><i></i>Ledgerly</div>
  </div>
</section>

<footer>
  <div class="abs footer"></div>
  <div class="abs fcol" style="left:60px">
    <h4>Newsletter Signup</h4>
    <div class="field">Name</div>
    <div class="field">Email</div>
    <span class="sub">Subscribe</span>
  </div>
  <div class="abs fcol" style="left:400px">
    <h4>Quick Links</h4>
    <div class="links">
      <ul><li>Home</li><li>About Us</li><li>Services</li><li>Technology</li></ul>
      <ul><li>Solutions</li><li>Support</li><li>Contact Us</li></ul>
    </div>
  </div>
  <div class="abs contact-box">
    <em>CONTACT US</em>
    <svg width="24" height="24" viewBox="0 0 24 24"><circle cx="12" cy="12" r="12" fill="#f08a1c"/><path d="M8.5 6.5l2 2-1.2 1.6c.7 1.6 2 2.9 3.6 3.6l1.6-1.2 2 2-1.4 2c-4 0-8.6-4.6-8.6-8.6z" fill="#fff"/></svg>
    <strong>123-456-7890</strong>
  </div>
  <div class="abs fcol" style="left:890px">
    <h4>Location Map</h4>
    <div class="map" role="img" aria-label="Street map showing the office location"></div>
  </div>
  <div class="abs bottom">
    <span>© 2014 HCSG. All Rights Reserved.</span>
    <div class="social"><span></span><span></span><span></span><span></span></div>
  </div>
</footer>

</body>
</html>
```